Real Estate investment company needs billboard designs

This is our website: https://brightlanepropertygroup.com/
We are looking for some billboard concepts that uses our CEO in the design. I have attached some images and 1 billboard design that someone in our industry uses, but we don't want it exactly like his.

Industry/Entity Type

real estate

Colors

Designer to choose colors to be used in the design.

Requirements
Must have
• Company colors from websiute

```html
<!DOCTYPE html>
<html lang="en">
<head>
<meta charset="utf-8">
<title>Brightlane Property Group – Billboard</title>
<link href="https://fonts.googleapis.com/css2?family=Oswald:wght@700&family=Montserrat:wght@600;800&family=Catamaran:wght@700&display=swap" rel="stylesheet">
<style>
  :root {
    --page-bg: #e4e2e3;
    --brand-red: #fe0c10;
    --brand-navy: #1b1c40;
    --white: #ffffff;
    --photo-dark: #2b2b2e;
    --photo-mid: #6b5a52;
    --bill-green: #b9cfa4;
  }
  html, body {
    margin: 0;
    padding: 0;
    width: 1011px;
    height: 1200px;
    overflow: hidden;
    background: var(--page-bg);
  }
  .billboard {
    position: absolute;
    left: 30px;
    top: 380px;
    width: 951px;
    height: 441px;
    background: var(--brand-red);
    overflow: hidden;
    box-shadow: 0 18px 40px rgba(0,0,0,0.28);
  }
  .billboard p, .billboard h1 { white-space: nowrap; }
  .brand-name {
    position: absolute;
    left: 40px;
    top: 40px;
    color: var(--white);
    font-family: "Montserrat", sans-serif;
    font-weight: 800;
    line-height: 1;
  }
  .brand-name .brand-main { display: block; font-size: 25px; letter-spacing: 0.5px; }
  .brand-name .brand-sub { display: block; font-size: 10px; letter-spacing: 1.6px; margin-top: 5px; }
  .ceo-photo {
    position: absolute;
    left: 28px;
    top: 112px;
    width: 256px;
    height: 329px;
    border-radius: 110px 110px 0 0;
    background: linear-gradient(180deg, var(--photo-mid) 0%, var(--photo-dark) 45%, var(--photo-dark) 100%);
  }
  .headline {
    position: absolute;
    left: 214px;
    top: 15px;
    width: 720px;
    margin: 0;
    text-align: center;
    color: var(--white);
    font-family: "Oswald", sans-serif;
    font-weight: 700;
    font-size: 138px;
    line-height: 1;
    letter-spacing: 1px;
  }
  .subhead {
    position: absolute;
    left: 294px;
    top: 158px;
    width: 560px;
    margin: 0;
    text-align: center;
    color: var(--brand-navy);
    font-family: "Montserrat", sans-serif;
    font-weight: 800;
    font-size: 59px;
    line-height: 1;
  }
  .tagline {
    position: absolute;
    left: 294px;
    top: 220px;
    width: 560px;
    margin: 0;
    text-align: center;
    color: var(--white);
    font-family: "Catamaran", sans-serif;
    font-weight: 700;
    font-size: 37px;
    line-height: 1.1;
  }
  .cash-bill {
    position: absolute;
    background: var(--bill-green);
    border-radius: 3px;
  }
  .cash-bill.left { left: 266px; top: 192px; width: 58px; height: 22px; transform: rotate(-18deg); }
  .cash-bill.right { left: 806px; top: 212px; width: 100px; height: 34px; transform: rotate(16deg); }
  .phone-band {
    position: absolute;
    left: 268px;
    top: 272px;
    right: 0;
    height: 79px;
    background: var(--brand-navy);
  }
  .phone-number {
    position: absolute;
    left: 272px;
    top: 272px;
    width: 604px;
    height: 79px;
    margin: 0;
    text-align: center;
    color: var(--white);
    font-family: "Montserrat", sans-serif;
    font-weight: 800;
    font-size: 54px;
    line-height: 79px;
    letter-spacing: 8px;
  }
  .website {
    position: absolute;
    left: 274px;
    top: 355px;
    width: 600px;
    margin: 0;
    text-align: center;
    color: var(--white);
    font-family: "Montserrat", sans-serif;
    font-weight: 600;
    font-size: 35px;
    line-height: 50px;
  }
</style>
</head>
<body>
  <main class="billboard">
    <div class="brand-name">
      <span class="brand-main">BRIGHTLANE</span>
      <span class="brand-sub">PROPERTY GROUP</span>
    </div>

    <div class="ceo-photo" role="img" aria-label="Photo of the company CEO in a dark polo shirt, arms crossed"></div>

    <h1 class="headline">CA$H OFFER</h1>
    <p class="subhead">ON SAME DAY</p>
    <p class="tagline">On Selling Your Home</p>

    <div class="cash-bill left" role="img" aria-label="Illustration of a floating dollar bill"></div>
    <div class="cash-bill right" role="img" aria-label="Illustration of a floating hundred dollar bill"></div>

    <div class="phone-band"></div>
    <p class="phone-number">865-555-0142</p>
    <p class="website">brightlanepropertygroup.com</p>
  </main>
</body>
</html>
```